Business card design Needed for new logo / Construction business, home extensions and new builds

We need a business card design using our new logo files which i will attach to this project :)

We are a small construction business specialising in home extensions, new builds and property development. We are very ambitious and would appreciate professional and elegant designs for our new business card.

Very serious about using the services on MakerQuarry and recently acquired our new logo from here :)

Please get involved, i will feedback when i can as i am very busy but can respond daily, thanks

Target Market(s)

People that want to build onto their houses, new building developments or adding too their existing property

Industry/Entity Type

Construction

Contact Information for Business Card

Renwick Tolliver Construction, Lionel Ashby (Managing Director), Tel 07822254961, email - info@renwick-tolliver, www.renwick-tolliver.co.uk

Colors

Designer to choose colors to be used in the design.

Requirements
Must have
• I like a deep grey on the back please. A lot of you have provided black from and back, try mixing things up a little. The black looks cool 😎 Thanks

```html
<!DOCTYPE html>
<html lang="en">
<head>
<meta charset="utf-8">
<title>Renwick Tolliver Construction – Business Card</title>
<link rel="stylesheet" href="https://fonts.googleapis.com/css2?family=Cinzel:wght@500&family=Montserrat:wght@400;700&display=swap">
<style>
  :root {
    --stage: #2b2b2d;
    --card-deep: #38383c;
    --card-deep-2: #2f2f33;
    --card-grey: #858585;
    --panel-black: #1c1d1d;
    --gold: #d9a32c;
    --silver: #c9ccd1;
    --text-light: #f4f4f4;
  }
  * { margin: 0; padding: 0; box-sizing: border-box; }
  html, body { width: 1200px; height: 689px; overflow: hidden; background: var(--stage); }
  .canvas {
    position: relative; width: 1200px; height: 689px;
    display: flex; align-items: center; justify-content: center; gap: 40px;
  }
  .card {
    position: relative; width: 540px; height: 310px;
    border-radius: 16px; overflow: hidden;
    box-shadow: 0 14px 34px rgba(0,0,0,0.45);
  }

  /* Front face */
  .card-front { background: var(--card-deep); }
  .front-pattern {
    position: absolute; inset: 0;
    background: linear-gradient(135deg, var(--card-deep) 0%, var(--card-deep-2) 100%);
  }
  .front-brand {
    position: absolute; inset: 0;
    display: flex; flex-direction: column; align-items: center; justify-content: center; gap: 14px;
  }
  .brand-mark { width: 22px; height: 22px; background: var(--gold); flex: none; }
  .brand-name {
    font-family: "Cinzel", serif; font-weight: 500; color: var(--gold);
    text-transform: uppercase; line-height: 1.25;
  }
  .front-brand .brand-name { font-size: 30px; letter-spacing: 2px; text-align: center; }

  /* Back face */
  .card-back { background: var(--card-grey); }
  .back-shapes { position: absolute; inset: 0; }
  .back-brand-left {
    position: absolute; left: 34px; top: 32px; width: 250px;
    display: flex; align-items: center; gap: 10px;
  }
  .back-brand-left .brand-name { font-size: 16px; letter-spacing: 1px; text-align: left; }
  .back-brand-left .brand-mark { width: 16px; height: 16px; }
  .back-brand-right {
    position: absolute; right: 18px; top: 92px; width: 172px;
    display: flex; flex-direction: column; align-items: center; gap: 10px;
  }
  .back-brand-right .brand-name { font-size: 16px; letter-spacing: 1px; text-align: center; }
  .back-brand-right .brand-mark { width: 16px; height: 16px; }

  .contact {
    position: absolute; left: 34px; bottom: 30px;
    font-family: "Montserrat", sans-serif; color: var(--text-light);
  }
  .person-name { font-weight: 700; font-size: 22px; color: var(--gold); }
  .person-role { font-size: 13px; margin-top: 2px; margin-bottom: 16px; }
  .contact-list { list-style: none; font-size: 12.5px; line-height: 1.75; }
  .contact-list li { display: flex; align-items: center; gap: 9px; }
  .contact-icon { width: 12px; height: 12px; flex: none; }
</style>
</head>
<body>
<main class="canvas">

  <section class="card card-front">
    <div class="front-pattern" role="img" aria-label="Subtle embossed repeating brand pattern in deep grey"></div>
    <div class="front-brand">
      <span class="brand-mark"></span>
      <p class="brand-name">Renwick Tolliver<br>Construction</p>
    </div>
  </section>

  <section class="card card-back">
    <svg class="back-shapes" width="540" height="310" viewBox="0 0 540 310">
      <path d="M350 0 C300 110 350 250 500 310 L540 310 L540 0 Z" fill="var(--panel-black)"/>
      <path d="M336 0 C286 110 336 250 486 310" fill="none" stroke="var(--silver)" stroke-width="8"/>
      <path d="M318 70 C310 170 370 270 470 310 L430 310 C350 270 316 180 318 70 Z" fill="var(--gold)"/>
    </svg>

    <div class="back-brand-left">
      <span class="brand-mark"></span>
      <p class="brand-name">Renwick Tolliver<br>Construction</p>
    </div>

    <div class="back-brand-right">
      <span class="brand-mark"></span>
      <p class="brand-name">Renwick Tolliver<br>Construction</p>
    </div>

    <div class="contact">
      <p class="person-name">Lionel Ashby</p>
      <p class="person-role">Managing Director</p>
      <ul class="contact-list">
        <li>
          <svg class="contact-icon" viewBox="0 0 12 12"><path d="M2 1 L4.5 1 L5.5 3.5 L4 4.6 C4.7 6 6 7.3 7.4 8 L8.5 6.5 L11 7.5 L11 10 C11 10.6 10.6 11 10 11 C5 10.6 1.4 7 1 2 C1 1.4 1.4 1 2 1 Z" fill="var(--gold)"/></svg>
          07822254961
        </li>
        <li>
          <svg class="contact-icon" viewBox="0 0 12 12"><rect x="0.5" y="2.5" width="11" height="7.5" rx="1" fill="var(--gold)"/><path d="M1 3 L6 7 L11 3" fill="none" stroke="var(--card-grey)" stroke-width="1"/></svg>
          info@renwick-tolliver
        </li>
        <li>
          <svg class="contact-icon" viewBox="0 0 12 12"><circle cx="6" cy="6" r="5.2" fill="var(--gold)"/><path d="M1 6 H11 M6 1 C3.5 4 3.5 8 6 11 M6 1 C8.5 4 8.5 8 6 11" fill="none" stroke="var(--card-grey)" stroke-width="0.8"/></svg>
          www.renwick-tolliver.co.uk
        </li>
      </ul>
    </div>
  </section>

</main>
</body>
</html>
```